We have a cheerleading competition on Sunday the 30 and I want to encourage parent assistance, support and participation!
Updates

1. Please add:
    Cheer Championship (instead of Cheerleading Competition)

2. Banner: Let's support our Cheerleaders!

Under Banner have the Date in big

Before the Location add:  Joins us at:

Thank you all for your designs and taking the time to submit them. I greatly appreciate them and they were all lovely. I could only pick one though! Hope to have you again on my next project.

Regards, Ramona

Industry/Entity Type

It Support

Requirements
Must have
• Flyer should be 1/2 of an A4 page. kid friendly. The cheerleaders are 6-13 yrs old.
The colors Burgundy, Gold (yellow) and White - It should have the team Eagle design on it. Dorrel Creek Ravens

Simple design. It will contain an address, times and dates.

should have all of the following information:

Date: Sunday - October 30th 2011
Location: Halvern Crest Arena at the Tolliver Ridge College
3872 Pellham Lane
Coral gables, FL 33146
Time: Tickets on sale 8:30AM - Doors Open 9:00AM Starts: 10:00AM
Prices: Adults $10.00 Children $5.00 - Cash Only

```html
<!DOCTYPE html>
<html lang="en">
<head>
<meta charset="utf-8">
<title>Cheer Championship Flyer</title>
<link href="https://fonts.googleapis.com/css2?family=Graduate&family=Staatliches&display=swap" rel="stylesheet">
<style>
  :root{
    --burgundy:#a8182c;
    --burgundy-dark:#7d1222;
    --paper:#ffffff;
    --frame:#d9dadb;
    --shadow:#1a1a1a;
    --pom-light:#f4d6d8;
    --pom-mid:#d9414f;
  }
  *{margin:0;padding:0;box-sizing:border-box}
  html,body{width:887px;height:1200px;overflow:hidden;background:var(--frame)}
  .canvas{position:relative;width:887px;height:1200px;background:var(--frame)}
  .flyer{position:absolute;left:64px;top:58px;width:760px;height:1080px;background:var(--paper);overflow:hidden}
  .flyer > *{position:absolute}
  .pompoms{top:232px;width:142px;height:586px;background:linear-gradient(180deg,var(--pom-light),var(--pom-mid) 30%,var(--pom-light) 50%,var(--pom-mid) 75%,var(--pom-light))}
  .pompoms--left{left:0;border-radius:0 60px 60px 0}
  .pompoms--right{right:0;width:126px;border-radius:60px 0 0 60px}
  .team-name{left:553px;top:34px;width:185px;text-align:center;font-family:"Staatliches",sans-serif;font-size:36px;line-height:38px;color:var(--burgundy)}
  .line{left:0;width:760px;text-align:center;white-space:nowrap;line-height:1.2}
  .outline{font-family:"Graduate",serif;color:var(--paper);-webkit-text-stroke:2px var(--burgundy)}
  .event-kicker{top:73px;font-size:66px;letter-spacing:2px}
  .event-title{top:147px;font-size:70px;letter-spacing:1px}
  .banner{font-family:"Graduate",serif;color:var(--burgundy);-webkit-text-stroke:3px var(--paper);paint-order:stroke fill;text-shadow:4px 5px 0 var(--shadow)}
  .banner--lets{top:225px;font-size:104px}
  .banner--support{top:312px;font-size:98px}
  .banner--our{top:396px;font-size:140px;transform:scaleX(1.15)}
  .banner--cheer{top:544px;font-size:59px;transform:rotate(2deg)}
  .date{top:631px;font-family:"Staatliches",sans-serif;font-size:66px;color:var(--burgundy-dark);letter-spacing:4px}
  .year{top:691px;font-size:62px}
  .weekday{top:758px;font-size:42px;letter-spacing:5px}
  .details{font-family:"Staatliches",sans-serif;color:var(--shadow)}
  .details--intro{top:839px;font-size:22px}
  .details--venue{top:856px;font-size:26px;letter-spacing:1.5px}
  .details--address{top:887px;font-size:26px;letter-spacing:1.5px}
  .schedule{top:939px;font-family:"Staatliches",sans-serif;font-size:30px;line-height:33px;color:var(--burgundy)}
  .schedule--times{right:344px;text-align:right}
  .schedule--prices{left:480px}
  .schedule b{font-weight:400;color:var(--burgundy-dark)}
</style>
</head>
<body>
<div class="canvas">
  <section class="flyer">
    <div class="pompoms pompoms--left" role="img" aria-label="Photo of cheerleaders' arms holding red and white pompoms"></div>
    <div class="pompoms pompoms--right" role="img" aria-label="Photo of cheerleaders' arms holding red and white pompoms"></div>
    <div class="team-name">Dorrel Creek Ravens</div>

    <h1 class="line outline event-kicker">CHEER</h1>
    <h2 class="line outline event-title">CHAMPIONSHIP</h2>

    <p class="line banner banner--lets">LET'S</p>
    <p class="line banner banner--support">SUPPORT</p>
    <p class="line banner banner--our">OUR</p>
    <p class="line banner banner--cheer">CHEERLEADERS!</p>

    <p class="line date">OCTOBER 30</p>
    <p class="line outline year">2011</p>
    <p class="line outline weekday">SUNDAY</p>

    <p class="line details details--intro">JOINS US AT:</p>
    <p class="line details details--venue">HALVERN CREST ARENA AT THE TOLLIVER RIDGE COLLEGE</p>
    <p class="line details details--address">3872 PELLHAM LANE CORAL GABLES, FL 33146</p>

    <div class="schedule schedule--times">
      <p>TICKETS ON SALE <b>8:30AM</b></p>
      <p>DOORS OPEN <b>9:00AM</b></p>
      <p>STARTS <b>10:00AM</b></p>
    </div>
    <div class="schedule schedule--prices">
      <p>ADULTS <b>$10.00</b></p>
      <p>CHILDREN <b>$5.00</b></p>
      <p><b>CASH ONLY</b></p>
    </div>
  </section>
</div>
</body>
</html>
```